Business Card Design for Occupational Medicine Start Up Company

We need to design a professional business card. We are a healthcare company providing occupational medicine services to blue collar industries. We are professional, efficient and high quality service providers.

Target Market(s)

Blue Collar Industry: Shipbuilding, Ports, Trucking Companies; The Executives and Safety Officers for these companies

Industry/Entity Type

Healthcare

Contact Information for Business Card

Logo, Name, Title, Email, Phone

Other font styles liked:
• Please match our Brand Guide

Requirements
Must have
• Our Company Colors and Logo

```html
<!DOCTYPE html>
<html lang="en">
<head>
<meta charset="utf-8">
<title>Crewline Clinics – Business Card</title>
<link href="https://fonts.googleapis.com/css2?family=Montserrat:wght@400;500;700&display=swap" rel="stylesheet">
<style>
  :root {
    --navy: #2b3282;
    --navy-deep: #232a73;
    --sky: #22a7e0;
    --amber: #f5b04c;
    --paper: #ffffff;
    --ink-grey: #5b5f68;
    --backdrop: #e6e7e9;
  }
  * { box-sizing: border-box; margin: 0; padding: 0; }
  html, body { width: 1200px; height: 896px; overflow: hidden; }
  body {
    background: var(--backdrop);
    font-family: "Montserrat", sans-serif;
    position: relative;
  }
  .card {
    position: absolute;
    left: 335px;
    width: 525px;
    height: 300px;
    border-radius: 30px;
    overflow: hidden;
    box-shadow: 0 14px 24px rgba(0,0,0,0.18);
  }
  .card--back { top: 126px; background: var(--navy); }
  .card--front { top: 475px; background: var(--paper); }

  .pattern-field {
    position: absolute; inset: 0;
    background: linear-gradient(125deg, var(--navy-deep) 0%, var(--navy) 45%, #4a62b0 100%);
  }

  .stripe { position: absolute; left: 0; width: 100%; height: 19px; }
  .stripe--amber { top: 0; background: var(--amber); }
  .stripe--navy { top: 19px; background: var(--navy); }
  .stripe--sky { top: 38px; background: var(--sky); }

  .mark-tab {
    position: absolute; left: 222px; top: 37px;
    width: 81px; height: 50px;
    background: var(--paper);
    border-radius: 22px 22px 0 0;
  }
  .mark-dot {
    position: absolute; left: 243px; top: 55px;
    width: 40px; height: 40px; border-radius: 50%;
    background: var(--sky);
  }
  .brand-name {
    position: absolute; left: 0; top: 112px; width: 100%;
    text-align: center;
    color: var(--navy);
    font-weight: 700;
    font-size: 22px;
    letter-spacing: 1px;
  }

  .identity {
    position: absolute; right: 290px; top: 212px;
    text-align: right;
  }
  .identity__name {
    color: var(--navy); font-weight: 700; font-size: 19px; letter-spacing: 0.4px;
  }
  .identity__title {
    color: var(--ink-grey); font-size: 13px; margin-top: 4px; font-weight: 500;
  }
  .divider {
    position: absolute; left: 256px; top: 207px;
    width: 1px; height: 53px; background: var(--amber);
  }
  .contacts {
    position: absolute; left: 275px; top: 205px;
    list-style: none;
  }
  .contacts li {
    display: flex; align-items: center; gap: 7px;
    height: 20px;
    color: var(--ink-grey); font-size: 13.5px; font-weight: 500;
  }
  .contacts svg { width: 11px; height: 11px; flex: none; }
</style>
</head>
<body>
  <section class="card card--back">
    <div class="pattern-field" role="img" aria-label="Repeating brand symbol pattern on navy, with one highlighted symbol"></div>
  </section>

  <section class="card card--front">
    <div class="stripe stripe--amber"></div>
    <div class="stripe stripe--navy"></div>
    <div class="stripe stripe--sky"></div>
    <div class="mark-tab"></div>
    <div class="mark-dot"></div>
    <div class="brand-name">CREWLINE CLINICS</div>

    <div class="identity">
      <div class="identity__name">MARK ELLISON</div>
      <div class="identity__title">President</div>
    </div>
    <div class="divider"></div>
    <ul class="contacts">
      <li>
        <svg viewBox="0 0 12 12" aria-hidden="true"><path d="M2.5 1 L4.5 1 L5.3 3.5 L4 4.6 Q5.2 7 7.4 8 L8.5 6.7 L11 7.5 L11 9.5 Q10.5 11 9 11 Q2 10 1 3 Q1 1.5 2.5 1Z" fill="var(--sky)"/></svg>
        555-014-2871
      </li>
      <li>
        <svg viewBox="0 0 12 12" aria-hidden="true"><rect x="0.5" y="2" width="11" height="8" rx="1" fill="var(--sky)"/><path d="M1 2.6 L6 6.5 L11 2.6" stroke="#fff" stroke-width="1" fill="none"/></svg>
        mark@crewlineclinics.com
      </li>
      <li>
        <svg viewBox="0 0 12 12" aria-hidden="true"><circle cx="6" cy="6" r="5.5" fill="var(--sky)"/><path d="M0.5 6 H11.5 M6 0.5 V11.5 M6 0.5 Q2.5 6 6 11.5 M6 0.5 Q9.5 6 6 11.5" stroke="#fff" stroke-width="0.7" fill="none"/></svg>
        www.crewlineclinics.com
      </li>
    </ul>
  </section>
</body>
</html>
```